BRN website video quote promotion tiles

We are promoting vehicle leasing by video, which contains several quotation examples imported from the video. We must re-vamp the quotation tiles, contact boxes, and contact form. The first tile is generated from the video, so this must be a separate project. We are looking for a welcoming, professional flow and leave color choices to design with an emphasis on communication prompts, and additional prompts in the design would be welcome.

Target Market(s)

Any Customer interaction from the tile quotes, contact, call, message,

Industry/Entity Type

vehicle leasing

Coding

Coded - Design and coding required

Number of Pages Required

1 page

Colors

Designer to choose colors to be used in the design.

Requirements
Must have
• emphasis on point of contact and visual impact on quote tile excluding main one
Should not have
• changes to the quote structure as these imported from video pricing no changes to main image as this template which can addressed as separate project

```html
<!DOCTYPE html>
<html lang="en">
<head>
<meta charset="utf-8">
<title>Vehicle Lease Offers</title>
<link href="https://fonts.googleapis.com/css2?family=Montserrat:wght@600;700&family=Nunito:wght@400;600;700;800&display=swap" rel="stylesheet">
<style>
:root{
  --ink:#444444;
  --orange:#E07F33;
  --green:#66A845;
  --red:#D8262B;
  --cream:#FAF4EF;
  --band:#F4F4F4;
  --white:#FFFFFF;
}
*{box-sizing:border-box;margin:0;padding:0}
html,body{width:844px;height:1200px;overflow:hidden;background:var(--white)}
body{position:relative;font-family:'Nunito',sans-serif;color:var(--ink)}
.section{position:absolute;left:0;width:844px}
.offers-light{top:0;height:430px;background:var(--white)}
.offers-dark{top:430px;height:418px;background:var(--band)}
.contact{top:848px;height:352px;background:var(--white)}
.section-title{position:absolute;left:0;width:844px;text-align:center;font-family:'Montserrat',sans-serif;font-weight:700;font-size:29px;line-height:1;color:var(--ink)}
.section-title::after{content:"";position:absolute;left:396px;width:53px;height:2px;background:var(--orange);bottom:-8px}
.offers-light .section-title{top:58px}
.offers-dark .section-title{top:56px}
.contact .section-title{top:58px;font-size:30px}
.tile{position:absolute;width:214px;text-align:center}
.tile-title{font-family:'Montserrat',sans-serif;font-weight:700;font-size:16px;letter-spacing:.1px}
.price{position:absolute;left:0;width:100%;font-family:'Montserrat',sans-serif;font-weight:700;font-size:20px;line-height:1}
.terms{position:absolute;left:24px;right:24px;font-size:13px;line-height:18px}
.status{position:absolute;left:0;width:100%;font-size:11px;color:var(--red);line-height:1}
.actions{position:absolute;left:13px;display:flex;gap:5px}
.btn-contact{width:144px;height:36px;border-radius:18px;font-family:'Nunito',sans-serif;font-weight:800;font-size:12.5px;display:flex;align-items:center;justify-content:center;letter-spacing:.2px}
.btn-chat{width:36px;height:36px;border-radius:50%;background:var(--green);display:flex;align-items:center;justify-content:center}
.tile--light{top:122px;height:234px;background:var(--white);border-radius:15px;box-shadow:0 4px 12px rgba(0,0,0,.16)}
.tile--light.is-active{border:1.5px solid var(--orange)}
.tile--light .tile-head{position:absolute;left:6px;right:6px;top:6px;height:48px;background:var(--cream);border-radius:13px;display:flex;align-items:center;justify-content:center;color:var(--orange)}
.tile--light .price{top:66px;color:var(--green)}
.tile--light .vat{position:absolute;top:92px;left:0;width:100%;font-family:'Montserrat',sans-serif;font-weight:700;font-size:8px}
.tile--light .terms{top:115px}
.tile--light .status{top:155px}
.tile--light .actions{top:190px}
.tile--light .btn-contact{border:1.5px solid var(--orange);color:var(--ink);background:var(--white)}
.tile--light.is-active .btn-contact{background:var(--orange);color:var(--white)}
.tile--framed{top:573px;height:217px;background:var(--white);border:1.5px solid var(--ink);border-radius:15px;box-shadow:0 4px 10px rgba(0,0,0,.14)}
.tile--framed .tile-head{position:absolute;left:16px;top:-25px;width:178px;height:48px;background:var(--ink);border-radius:18px;display:flex;align-items:center;justify-content:center;color:var(--white)}
.tile--framed .price{top:40px;color:var(--orange)}
.tile--framed .vat{position:absolute;top:65px;left:73px;width:65px;height:22px;border:1.5px solid var(--green);border-radius:11px;color:var(--green);font-family:'Montserrat',sans-serif;font-weight:700;font-size:8px;display:flex;align-items:center;justify-content:center}
.tile--framed .terms{top:96px}
.tile--framed .status{top:141px;text-decoration:underline;text-underline-offset:2px}
.tile--framed .actions{top:168px}
.tile--framed .btn-contact{background:var(--cream);color:var(--orange)}
.tile--framed.is-active .btn-contact{background:var(--orange);color:var(--white)}
.col-1{left:78px}.col-2{left:316px}.col-3{left:553px}
.field{position:absolute;background:var(--white);box-shadow:0 2px 8px rgba(0,0,0,.12);border-radius:3px;font-size:11px;color:var(--ink);padding:0 13px;display:flex;align-items:center}
.field--name{left:107px;top:121px;width:205px;height:35px}
.field--email{left:320px;top:121px;width:205px;height:35px}
.field--phone{left:533px;top:121px;width:205px;height:35px}
.field--message{left:107px;top:166px;width:631px;height:77px;align-items:flex-start;padding-top:12px}
.btn-submit{position:absolute;left:350px;top:255px;width:144px;height:36px;border-radius:18px;background:var(--orange);color:var(--white);font-weight:800;font-size:12.5px;display:flex;align-items:center;justify-content:center}
</style>
</head>
<body>

<section class="section offers-light">
  <h2 class="section-title">Our Offers</h2>
  <article class="tile tile--light col-1">
    <div class="tile-head"><span class="tile-title">CONTRACT HIRE</span></div>
    <div class="price">£247.33</div><div class="vat">PLUS VAT</div>
    <p class="terms">3 years, 9+35, 10K miles annually</p>
    <p class="status">Not Maintained</p>
    <div class="actions"><span class="btn-contact">CONTACT US</span><span class="btn-chat"><svg width="18" height="18" viewBox="0 0 24 24"><path fill="#fff" d="M6.6 10.8a15.1 15.1 0 0 0 6.6 6.6l2.2-2.2a1 1 0 0 1 1-.25 11.4 11.4 0 0 0 3.6.57 1 1 0 0 1 1 1V20a1 1 0 0 1-1 1A17 17 0 0 1 3 4a1 1 0 0 1 1-1h3.5a1 1 0 0 1 1 1c0 1.25.2 2.45.57 3.57a1 1 0 0 1-.25 1z"/></svg></span></div>
  </article>
  <article class="tile tile--light col-2 is-active">
    <div class="tile-head"><span class="tile-title">CONTRACT HIRE</span></div>
    <div class="price">£247.33</div><div class="vat">PLUS VAT</div>
    <p class="terms">3 years, 9+35, 10K miles annually</p>
    <p class="status">Not Maintained</p>
    <div class="actions"><span class="btn-contact">CONTACT US</span><span class="btn-chat"><svg width="18" height="18" viewBox="0 0 24 24"><path fill="#fff" d="M6.6 10.8a15.1 15.1 0 0 0 6.6 6.6l2.2-2.2a1 1 0 0 1 1-.25 11.4 11.4 0 0 0 3.6.57 1 1 0 0 1 1 1V20a1 1 0 0 1-1 1A17 17 0 0 1 3 4a1 1 0 0 1 1-1h3.5a1 1 0 0 1 1 1c0 1.25.2 2.45.57 3.57a1 1 0 0 1-.25 1z"/></svg></span></div>
  </article>
  <article class="tile tile--light col-3">
    <div class="tile-head"><span class="tile-title">CONTRACT HIRE</span></div>
    <div class="price">£247.33</div><div class="vat">PLUS VAT</div>
    <p class="terms">3 years, 9+35, 10K miles annually</p>
    <p class="status">Not Maintained</p>
    <div class="actions"><span class="btn-contact">CONTACT US</span><span class="btn-chat"><svg width="18" height="18" viewBox="0 0 24 24"><path fill="#fff" d="M6.6 10.8a15.1 15.1 0 0 0 6.6 6.6l2.2-2.2a1 1 0 0 1 1-.25 11.4 11.4 0 0 0 3.6.57 1 1 0 0 1 1 1V20a1 1 0 0 1-1 1A17 17 0 0 1 3 4a1 1 0 0 1 1-1h3.5a1 1 0 0 1 1 1c0 1.25.2 2.45.57 3.57a1 1 0 0 1-.25 1z"/></svg></span></div>
  </article>
</section>

<section class="section offers-dark">
  <h2 class="section-title">Our Offers</h2>
</section>
<article class="tile tile--framed col-1">
  <div class="tile-head"><span class="tile-title">CONTRACT HIRE</span></div>
  <div class="price">£247.33</div><div class="vat">PLUS VAT</div>
  <p class="terms">3 years, 9+35, 10K miles annually</p>
  <p class="status">Not Maintained</p>
  <div class="actions"><span class="btn-contact">CONTACT US</span><span class="btn-chat"><svg width="18" height="18" viewBox="0 0 24 24"><path fill="#fff" d="M6.6 10.8a15.1 15.1 0 0 0 6.6 6.6l2.2-2.2a1 1 0 0 1 1-.25 11.4 11.4 0 0 0 3.6.57 1 1 0 0 1 1 1V20a1 1 0 0 1-1 1A17 17 0 0 1 3 4a1 1 0 0 1 1-1h3.5a1 1 0 0 1 1 1c0 1.25.2 2.45.57 3.57a1 1 0 0 1-.25 1z"/></svg></span></div>
</article>
<article class="tile tile--framed col-2">
  <div class="tile-head"><span class="tile-title">CONTRACT HIRE</span></div>
  <div class="price">£247.33</div><div class="vat">PLUS VAT</div>
  <p class="terms">3 years, 9+35, 10K miles annually</p>
  <p class="status">Not Maintained</p>
  <div class="actions"><span class="btn-contact">CONTACT US</span><span class="btn-chat"><svg width="18" height="18" viewBox="0 0 24 24"><path fill="#fff" d="M6.6 10.8a15.1 15.1 0 0 0 6.6 6.6l2.2-2.2a1 1 0 0 1 1-.25 11.4 11.4 0 0 0 3.6.57 1 1 0 0 1 1 1V20a1 1 0 0 1-1 1A17 17 0 0 1 3 4a1 1 0 0 1 1-1h3.5a1 1 0 0 1 1 1c0 1.25.2 2.45.57 3.57a1 1 0 0 1-.25 1z"/></svg></span></div>
</article>
<article class="tile tile--framed col-3 is-active">
  <div class="tile-head"><span class="tile-title">CONTRACT HIRE</span></div>
  <div class="price">£247.33</div><div class="vat">PLUS VAT</div>
  <p class="terms">3 years, 9+35, 10K miles annually</p>
  <p class="status">Not Maintained</p>
  <div class="actions"><span class="btn-contact">CONTACT US</span><span class="btn-chat"><svg width="18" height="18" viewBox="0 0 24 24"><path fill="#fff" d="M6.6 10.8a15.1 15.1 0 0 0 6.6 6.6l2.2-2.2a1 1 0 0 1 1-.25 11.4 11.4 0 0 0 3.6.57 1 1 0 0 1 1 1V20a1 1 0 0 1-1 1A17 17 0 0 1 3 4a1 1 0 0 1 1-1h3.5a1 1 0 0 1 1 1c0 1.25.2 2.45.57 3.57a1 1 0 0 1-.25 1z"/></svg></span></div>
</article>

<section class="section contact">
  <h2 class="section-title">Contact Us</h2>
  <div class="field field--name">Your Name</div>
  <div class="field field--email">Email</div>
  <div class="field field--phone">Contact Number</div>
  <div class="field field--message">Message</div>
  <div class="btn-submit">SUBMIT</div>
</section>

</body>
</html>
```